Custom Woodworking and Rock Design

We specialize in original, high quality, wood and rock art. It’s should be self explanatory ask questions if you need. Your team designing a logo. Furniture is custom made to order. Rocks are designed depending on consumer needs. Wood and rock can also be combined for custom work. Painted rocks on vintage wood. Custom chairs and cabinets. Artistic rocks for multiple uses:garden, magnets, custom. All ideas and requests are welcome.

Target Market(s)

All

Contact Information for Business Card

Mara Voss
Talbertstonecraft@mailbrook.net

Font styles to use
Sans Serif

Requirements
Must have
• Clear lettering
Nice to have
• Eye catching
Should not have
• Blurr

```html
<!DOCTYPE html>
<html lang="en">
<head>
<meta charset="UTF-8">
<title>Mara Voss — Business Card</title>
<link href="https://fonts.googleapis.com/css2?family=Montserrat:wght@400;600&display=swap" rel="stylesheet">
<style>
  :root {
    --page-bg: #e9e6e2;
    --wood-light: #a8643a;
    --wood-mid: #8c4f2b;
    --wood-dark: #6e3a1e;
    --band-blue: #3f6ab8;
    --band-blue-light: #5a84cc;
    --text-white: #ffffff;
    --rule-white: rgba(255, 255, 255, 0.85);
  }
  * { margin: 0; padding: 0; box-sizing: border-box; }
  html, body {
    width: 1200px;
    height: 900px;
    overflow: hidden;
    background: var(--page-bg);
  }
  .business-card {
    position: absolute;
    left: 75px;
    top: 150px;
    width: 1050px;
    height: 600px;
    overflow: hidden;
    font-family: "Montserrat", sans-serif;
  }
  .wood-panel {
    position: absolute;
    left: 0;
    width: 100%;
    background: linear-gradient(100deg, var(--wood-mid) 0%, var(--wood-light) 45%, var(--wood-mid) 75%, var(--wood-dark) 100%);
  }
  .wood-panel--top { top: 0; height: 260px; }
  .wood-panel--bottom { top: 390px; height: 210px; }
  .name-band {
    position: absolute;
    left: 0;
    top: 260px;
    width: 100%;
    height: 130px;
    background: linear-gradient(90deg, var(--band-blue) 0%, var(--band-blue-light) 55%, var(--band-blue) 100%);
    display: flex;
    flex-direction: column;
    align-items: center;
    justify-content: center;
    gap: 14px;
    color: var(--text-white);
  }
  .name-row {
    display: flex;
    align-items: center;
    gap: 14px;
  }
  .name-rule {
    width: 150px;
    height: 1.5px;
    background: var(--rule-white);
    margin-top: 22px;
  }
  .holder-name {
    font-weight: 600;
    font-size: 46px;
    letter-spacing: 1px;
    line-height: 1;
  }
  .holder-email {
    font-weight: 400;
    font-size: 26px;
    letter-spacing: 1px;
    line-height: 1;
  }
</style>
</head>
<body>
  <div class="business-card">
    <div class="wood-panel wood-panel--top" role="img" aria-label="Warm brown wood grain texture"></div>
    <div class="name-band">
      <div class="name-row">
        <span class="name-rule"></span>
        <h1 class="holder-name">Mara Voss</h1>
        <span class="name-rule"></span>
      </div>
      <p class="holder-email">Talbertstonecraft@mailbrook.net</p>
    </div>
    <div class="wood-panel wood-panel--bottom" role="img" aria-label="Warm brown wood grain texture"></div>
  </div>
</body>
</html>
```